Snapnook needs You

Help us create an inviting, amazing, sleek, simple, clear landing page for a picture-memory-social connection site!

Business Name: SnapNook
Industry: Social Networking and Creativity through Pictures
A web platform for and about a community that is driven by a passion for sharing, caring, bonding, collaborating, creating and earning with pictures, through pictures and other related creative activities. This is going to be a great site for all creative artists-photographers, artists, graphic artists to express their work and their creativity.

The main focus of the site is - CONNECTIONS.
This will be uncoded.

Desired Website Screen Size
1024x768... Widescreen/Landscape orientation, is what we mean... So it fits on a CPU screen.

Desired look and feel and message
Look: Visitor should feel immersed in the page, in the world the page creates, simple, elegant, sophisticated, contemporary. We really like a clean uncluttered look.

Special mention: By the way we love the marketing genius who thought up this branding for velu yogurt where they used the two dots above the o to create a branding effect that made this brand instantly identifiable. http://www.velu-dairy.ca/en/

The two dots by themselves without having even the name present brings up the whole brand now. The dots are used above all the ingredients of the yogurt creating friendly figures, and above people in commercials-bringing the people onto the side of "team" velu. Snapnook may have a character created or something distinctive in the letters in the name created to brand the site as well.

Feel: Engaging; Magical without being corny, here is a link to give an example look and feel but please do not be hindered in your creativity by this suggestion. We love all creative angles.
http://artscrapyard.com/graphic/5829317-camera-film-roll-blue-background

Message: Life and memories and connections through pictures.

Target audience:
The site is focused on pictures but not confined to photography enthusiasts (although they are an integral part of the site). Customers/Visitors will include families, corporates and the younger generation - all age groups, all class, everyone with pictures to express, memories to share.

Website design we like:
http://brindlework.com/work/northern-ballet-house/
http://brindlework.com/work/zapverse/

What colors do we want to see on our landing page?
We would like the background to be grey or blue since it is grey is picture neutral colour and blue highlights pictures well and we also like blue and silver, which can be integrated into the theme. Also like green. But please do not let these instructions limit your creativity. We are open to new ideas and colours.

Predetermined Concepts if any:
We have a concept in mind and we think it would be cool to have an interface for the user through the back of a camera on the landing page -This could be used to create a scene or world the visitor feels a part of or is immersed into. The back screen of the camera may act as a screen for the slideshow of featured pictures on the site.

Content on the Page:
Photo Gallery with full screen, thumbnail view, zoom option etc.
Prominent but short introductory message
Sign in / Login Options
Links: Home Page; About; Info/Help; Contact Us; Privacy Policy; Terms of Use
At the bottom of the page: Follow Me/Like/Workplaza...social buttons.

Please feel free to add any other element to the landing page that you think might add to the effect of simple yet amazing look -clean, simple, uncluttered, sophisticated, stylish, inviting and engaging.
The concept is a guideline, but we would like you to be as creative as you can, even if it meant stepping out of these guidelines - rethink design, style, content if you like. We believe in bringing a solution in an innovative yet simple and elegant style. Something a visitor would be intrigued enough to explore and the guest would feel comfortable enough taking that step forward to have fun on the site. If you believe in the same, and you have the skill then you will have what we need. Good luck, go for it and we are excited to see what the amazing designers on this amazing site have to offer.
If you have any questions please free to ask.

HI wanted to send an update that this project design has been guaranteed.

Our site will be one to celebrate and showcase imagination as well as connection.  We would love to see what you create. Keep in mind our site will showcase all creativity, photographs, artists, graphic artists so this would be a benefit you may want to take advantage of in the future, a place where, if you so choose, you could gain exposure for your work. Therefore, even if you do not win the design project there is possible future benefit.

Imagination is everything.
Imagination encircles the world.-Halvorsen

Reason: We are giving the designers who accepted invites but have not yet submitted a chance to finish their submissions and the ones who are working on revisions a chance to finish those:)

Hello everyone,

Due to time constraints we must come to a decision sooner than the deadline of 28th. 

So, please try to submit any new designs or modifications to the old ones before the 26th. We are very thankful to all of you who have participated - for your designs, enthusiasm and kind words. 

Good luck! :)

• Thank you for the interest shown and your submissions! Designers who have submitted up until now have shown great potential. We are VERY excited with the quality of work and designs.

We want to add that Snapnook is not exclusively for the photographers. The site is for every person who may have a picture to store, organise, use or share - whether publicly or with only a few friends and family.

Snapnook is about allowing people to take control of their creativity. It is about providing tools to our users so that they can build their own connections and social network... of friends, family, fans, clients, ideas, thoughts, emotions etc. through pictures without worrying about their privacy or control over their creations.

With this update we want to encourage others to go beyond the camera theme. Do not let us restrict your creativity. Let YOUR OWN ideas take over if that’s what you think will best convey the message and will appeal to the users.

```html
<!DOCTYPE html>
<html lang="en">
<head>
<meta charset="utf-8">
<title>SnapNook — Landing</title>
<link href="https://fonts.googleapis.com/css2?family=Arimo:ital,wght@0,400;0,700;1,400;1,700&display=swap" rel="stylesheet">
<style>
  :root {
    --accent-orange: #f39a1e;
    --button-orange: #e8730f;
    --nav-blue: #0ea1dd;
    --nav-blue-dark: #0a86bd;
    --go-blue: #1a86c8;
    --hero-top: #6b6b6b;
    --hero-bottom: #000;
    --band-top: #ffffff;
    --band-bottom: #d9d9d9;
    --footer: #2d2d2f;
    --text-light: #d4d4d4;
    --text-dark: #222;
    --text-muted: #555;
    --white: #fff;
  }
  * { box-sizing: border-box; margin: 0; padding: 0; }
  html, body { width: 1200px; height: 740px; overflow: hidden; }
  body { font-family: "Arimo", Arial, sans-serif; background: var(--footer); position: relative; }

  .top-rule { position: absolute; left: 0; top: 0; width: 1200px; height: 4px; background: var(--accent-orange); z-index: 3; }

  .hero { position: absolute; left: 0; top: 0; width: 1200px; height: 484px;
    background: linear-gradient(180deg, var(--hero-top) 0%, #3e3e3e 50%, var(--hero-bottom) 100%); overflow: hidden; }
  .hero-visual { position: absolute; left: 161px; top: 0; width: 834px; height: 484px;
    background: radial-gradient(ellipse at 55% 40%, rgba(150,150,150,.35) 0%, rgba(80,80,80,.15) 50%, rgba(0,0,0,0) 75%); }

  .brand { position: absolute; left: 213px; top: 58px; display: flex; align-items: baseline; gap: 12px; }
  .brand-name { font-size: 28px; font-weight: 400; color: var(--white); letter-spacing: .5px; }
  .brand-tag { font-size: 11px; font-style: italic; color: var(--white); }

  .social { position: absolute; left: 710px; top: 63px; display: flex; gap: 3px; }
  .social span { width: 14px; height: 14px; border-radius: 2px; background: #8b8b8b; }

  .search-icon { position: absolute; left: 792px; top: 62px; }
  .search { position: absolute; left: 817px; top: 58px; width: 183px; height: 23px; border-radius: 6px;
    background: #1e1e1e; border: 1px solid #555; color: #ddd; font-size: 14px; font-style: italic; padding: 3px 8px; }

  .intro { position: absolute; left: 395px; top: 220px; width: 430px; text-align: center; }
  .btn-signup { display: inline-block; width: 80px; height: 22px; line-height: 22px; border-radius: 3px;
    background: linear-gradient(180deg, #f28a22, var(--button-orange)); color: var(--white);
    font-size: 13px; font-style: italic; box-shadow: 0 1px 3px rgba(0,0,0,.5); }
  .intro-text { margin-top: 19px; font-size: 13.5px; line-height: 12.6px; font-style: italic; color: var(--text-light); }
  .free-trial { margin-top: 7px; font-size: 13.5px; font-style: italic; color: var(--text-light); letter-spacing: .5px; word-spacing: 3px; }

  .feature-band { position: absolute; left: 0; top: 484px; width: 1200px; height: 103px;
    background: linear-gradient(180deg, var(--band-top) 0%, #efefef 60%, var(--band-bottom) 100%);
    border-top: 1px solid #555; }
  .feature { position: absolute; top: 34px; }
  .feature-go { position: absolute; left: 0; top: 11px; width: 20px; height: 20px; border-radius: 50%;
    background: radial-gradient(circle at 40% 35%, #4cb3ea, var(--go-blue) 70%); color: var(--white);
    font-size: 8px; font-style: italic; text-align: center; line-height: 20px; }
  .feature-title { position: absolute; left: 28px; top: -4px; font-size: 22px; color: var(--text-dark); white-space: nowrap; }
  .feature-text { position: absolute; left: 24px; top: 20px; font-size: 12px; font-style: italic; color: var(--text-muted); white-space: nowrap; }
  .feature--one { left: 275px; }
  .feature--two { left: 634px; top: 32px; }

  .main-nav { position: absolute; left: 0; top: 587px; width: 1200px; height: 36px; background: var(--nav-blue); }
  .nav-tabs { position: absolute; left: 0; top: 0; }
  .nav-link { position: absolute; top: 8px; color: var(--white); font-size: 17px; }
  .nav-indicator { position: absolute; left: 333px; top: 30px; width: 16px; height: 12px; border-radius: 50%; background: #3a3a3a; }
  .signin-label { position: absolute; left: 744px; top: 9px; color: var(--white); font-size: 17px; font-style: italic; }
  .signin-email { position: absolute; left: 824px; top: 8px; width: 146px; height: 21px; border-radius: 5px;
    background: var(--nav-blue-dark); box-shadow: inset 0 1px 3px rgba(0,0,0,.4); color: var(--white);
    font-size: 14px; font-style: italic; padding: 2px 9px; }
  .signin-go { position: absolute; left: 980px; top: 9px; color: var(--white); font-size: 15px; font-style: italic; }

  .footer { position: absolute; left: 0; top: 623px; width: 1200px; height: 117px;
    background: radial-gradient(ellipse at 50% 0%, #444 0%, var(--footer) 60%); }
  .footer-line { position: absolute; left: 0; width: 1200px; top: 78px; text-align: center; white-space: nowrap; }
  .footer-note { font-size: 9.5px; font-style: italic; color: #aaa; }
  .footer-brand { font-size: 15px; color: var(--white); margin: 0 6px; }
</style>
</head>
<body>
  <div class="top-rule"></div>

  <header class="hero">
    <div class="hero-visual" role="img" aria-label="Soft monochrome photograph of large dimensional lettering spelling connection"></div>

    <div class="brand">
      <span class="brand-name">SNAPNOOK</span>
      <span class="brand-tag">PROFESHIONAL PHTO</span>
    </div>

    <div class="social" aria-label="Social links">
      <span></span><span></span><span></span><span></span>
    </div>

    <svg class="search-icon" width="18" height="18" viewBox="0 0 18 18" aria-hidden="true">
      <circle cx="11" cy="7" r="5" fill="none" stroke="#1ea7e8" stroke-width="2.5"/>
      <line x1="7.5" y1="10.5" x2="2" y2="16" stroke="#1ea7e8" stroke-width="3" stroke-linecap="round"/>
    </svg>
    <div class="search">Search</div>

    <section class="intro">
      <span class="btn-signup">SIGN UP</span>
      <p class="intro-text">Te dicam labitur mel, est eu graeco minimum, in sit facer assueverit incidérint. Laudem diceret no his, et mea minim nominati democri-tum, at quo partem<br>numquam feugiat. Liber primis maiestatis ius ut. Ius liber congue labo-ramus ne.</p>
      <p class="free-trial">FREE TRIAL</p>
    </section>
  </header>

  <section class="feature-band">
    <div class="feature feature--one">
      <span class="feature-go">GO</span>
      <span class="feature-title">SNAPNOOK</span>
      <span class="feature-text">Te dicam labitur mel, est eu graeco minimum,</span>
    </div>
    <div class="feature feature--two">
      <span class="feature-go">GO</span>
      <span class="feature-title">SNAPNOOK</span>
      <span class="feature-text">Te dicam labitur mel, est eu graeco minimum,</span>
    </div>
  </section>

  <nav class="main-nav">
    <svg class="nav-tabs" width="600" height="36" aria-hidden="true">
      <polygon points="210,0 300,0 292,36 200,36" fill="#1aaae5"/>
      <polygon points="302,0 392,0 384,36 294,36" fill="#1ba6e0"/>
      <polygon points="394,0 480,0 472,36 386,36" fill="#1aaae5"/>
      <polygon points="482,0 562,0 554,36 474,36" fill="#1ba6e0"/>
      <polygon points="200,0 210,0 200,36 190,36" fill="#0a7fb4"/>
      <polygon points="300,0 304,0 296,36 292,36" fill="#0a7fb4"/>
      <polygon points="392,0 396,0 388,36 384,36" fill="#0a7fb4"/>
      <polygon points="480,0 484,0 476,36 472,36" fill="#0a7fb4"/>
      <polygon points="562,0 568,0 560,36 554,36" fill="#0a7fb4"/>
    </svg>
    <a class="nav-link" style="left:229px">home</a>
    <a class="nav-link" style="left:313px">products</a>
    <a class="nav-link" style="left:413px">about</a>
    <a class="nav-link" style="left:498px">contact</a>
    <span class="nav-indicator"></span>

    <span class="signin-label">SIGN IN</span>
    <div class="signin-email">email</div>
    <span class="signin-go">GO</span>
  </nav>

  <footer class="footer">
    <p class="footer-line">
      <span class="footer-note">minimum, in sit facer assueverit incidérint.</span>
      <span class="footer-brand">SNAPNOOK</span>
      <span class="footer-note">minimum, in sit facer assueverit incidérint.</span>
    </p>
  </footer>
</body>
</html>
```